Golf Tournament Flyer and Header Needed

Non-profit needs a flyer for their benefit golf tournament - "Wild Socks Benefit Golf Classic"

Target Market(s)

Design and Construction industry professionals

Industry/Entity Type

Design and Construction

Colors

Designer to choose colors to be used in the design.

Requirements
Must have
• Date: September 22, 2021, 8:00 AM Shotgun Start, Location: Brookmere Links. O-VardeX Logo
Nice to have
• Would like image of golfers in crazy pants incorporated.

```html
<!DOCTYPE html>
<html lang="en">
<head>
<meta charset="utf-8">
<title>Wild Socks Benefit Golf Classic – Flyer</title>
<link href="https://fonts.googleapis.com/css2?family=Oswald:wght@700&family=Montserrat:wght@500;700;800&display=swap" rel="stylesheet">
<style>
  :root {
    --navy: #23409a;
    --green: #8ab833;
    --ink: #1f1f1f;
    --white: #ffffff;
    --paper: #f3f4f5;
    --sky: #5f9fe6;
    --tree: #3d6b2e;
    --fairway: #6aa83f;
    --coral: #f4606f;
    --teal: #46bfb6;
  }
  * { margin: 0; padding: 0; box-sizing: border-box; }
  html, body { width: 1027px; height: 1200px; overflow: hidden; background: #e9e9e9; }
  .flyer {
    position: relative; width: 1027px; height: 1200px; overflow: hidden;
    background: var(--paper);
    font-family: "Montserrat", Arial, sans-serif; color: var(--ink);
  }
  .photo-hero {
    position: absolute; left: 0; top: 0; width: 1027px; height: 780px;
    background: linear-gradient(180deg, var(--sky) 0%, #8cc0f0 26%, var(--tree) 40%, var(--fairway) 62%, #5b9634 100%);
  }
  .panel { position: absolute; inset: 0; width: 1027px; height: 1200px; }
  .photo-team {
    position: absolute; left: 580px; top: 735px; width: 447px; height: 465px;
    background: linear-gradient(180deg, var(--paper) 0%, #f58a95 16%, var(--coral) 36%, var(--teal) 64%, #3fae9e 82%, #6b9c45 100%);
  }
  .brand {
    position: absolute; left: 48px; top: 48px; display: flex; align-items: center; gap: 18px;
  }
  .brand-dot { width: 78px; height: 78px; border-radius: 50%; background: var(--navy); }
  .brand-name { font-weight: 800; font-size: 46px; color: var(--navy); letter-spacing: 1px; line-height: 1; }
  .brand-tag { font-weight: 700; font-size: 12.5px; color: var(--green); margin-top: 8px; }
  .title {
    position: absolute; left: 52px; top: 780px; width: 520px;
    font-family: "Oswald", Impact, sans-serif; font-weight: 700; letter-spacing: -0.5px;
  }
  .title-line1 { font-size: 54px; line-height: 1.08; color: var(--navy); }
  .title-line2 { font-size: 78px; line-height: 1.02; color: var(--green); }
  .info-row { position: absolute; left: 58px; display: flex; align-items: center; gap: 20px; }
  .info-row.date { top: 936px; }
  .info-row.place { top: 1024px; }
  .icon-badge {
    width: 74px; height: 74px; border-radius: 50%; background: var(--navy);
    border: 4px solid var(--white); box-shadow: 0 0 0 4px var(--green), 0 3px 7px rgba(0,0,0,.25);
    display: flex; align-items: center; justify-content: center; flex-shrink: 0;
  }
  .date-main { font-weight: 800; font-size: 29px; color: var(--navy); line-height: 1.1; }
  .date-sub { font-weight: 700; font-size: 22px; color: var(--ink); margin-top: 3px; }
  .place-name { font-weight: 700; font-size: 28px; color: var(--ink); }
  .contact { position: absolute; left: 50px; top: 1130px; color: var(--white); font-weight: 500; font-size: 18px; }
  .contact-line { display: flex; gap: 44px; align-items: center; margin-bottom: 9px; }
  .contact-item { display: flex; align-items: center; gap: 10px; }
</style>
</head>
<body>
<div class="flyer">
  <div class="photo-hero" role="img" aria-label="Photo of four golfers in white polos and blue diamond-pattern trousers on a tree-lined golf course"></div>
  <svg class="panel" viewBox="0 0 1027 1200" aria-hidden="true">
    <path d="M0 0 H560 C520 130 390 205 0 212 Z" fill="var(--white)"/>
    <path d="M0 212 C390 205 520 130 560 0" fill="none" stroke="var(--green)" stroke-width="9"/>
    <path d="M0 772 C260 700 660 680 1027 740 V1200 H0 Z" fill="var(--paper)"/>
  </svg>
  <div class="photo-team" role="img" aria-label="Photo of four golfers in coral polos and teal flamingo-print trousers standing on grass"></div>
  <svg class="panel" viewBox="0 0 1027 1200" aria-hidden="true">
    <path d="M0 772 C260 700 660 680 1027 740" fill="none" stroke="var(--green)" stroke-width="9"/>
    <path d="M0 1112 L650 1082 C612 1118 594 1160 588 1200 H0 Z" fill="var(--navy)"/>
    <path d="M588 1200 C602 1132 682 1084 800 1064" fill="none" stroke="var(--green)" stroke-width="7"/>
  </svg>

  <div class="brand">
    <div class="brand-dot"></div>
    <div>
      <div class="brand-name">O-VardeX</div>
      <div class="brand-tag">Organization for Value in Regional Design</div>
    </div>
  </div>

  <h1 class="title">
    <div class="title-line1">WILD SOCKS BENEFIT</div>
    <div class="title-line2">GOLF CLASSIC</div>
  </h1>

  <div class="info-row date">
    <div class="icon-badge">
      <svg width="40" height="40" viewBox="0 0 46 46" fill="none" stroke="#fff" stroke-width="3">
        <rect x="4" y="8" width="36" height="32" rx="3"/>
        <line x1="4" y1="17" x2="40" y2="17"/>
        <line x1="13" y1="3" x2="13" y2="11"/><line x1="31" y1="3" x2="31" y2="11"/>
        <g fill="#fff" stroke="none">
          <rect x="9" y="22" width="5" height="4"/><rect x="17" y="22" width="5" height="4"/><rect x="25" y="22" width="5" height="4"/>
          <rect x="9" y="30" width="5" height="4"/><rect x="17" y="30" width="5" height="4"/>
        </g>
        <circle cx="36" cy="36" r="8" fill="var(--navy)"/><path d="M36 32 V36 H39"/>
      </svg>
    </div>
    <div>
      <div class="date-main">September 22, 2021</div>
      <div class="date-sub">8:00 AM Shotgun Start</div>
    </div>
  </div>

  <div class="info-row place">
    <div class="icon-badge">
      <svg width="40" height="40" viewBox="0 0 46 46" fill="none" stroke="#fff" stroke-width="3">
        <path d="M23 32 C16 24 13 19 13 15 A10 10 0 0 1 33 15 C33 19 30 24 23 32 Z"/>
        <circle cx="23" cy="15" r="4"/>
        <ellipse cx="23" cy="36" rx="15" ry="5"/>
      </svg>
    </div>
    <div class="place-name">Brookmere Links</div>
  </div>

  <div class="contact">
    <div class="contact-line">
      <span class="contact-item">
        <svg width="20" height="20" viewBox="0 0 24 24" fill="var(--green)"><path d="M6.6 10.8a15 15 0 0 0 6.6 6.6l2.2-2.2a1 1 0 0 1 1-.25 11.4 11.4 0 0 0 3.6.57 1 1 0 0 1 1 1V20a1 1 0 0 1-1 1A17 17 0 0 1 3 4a1 1 0 0 1 1-1h3.5a1 1 0 0 1 1 1c0 1.25.2 2.45.57 3.6a1 1 0 0 1-.25 1z"/></svg>
        555-014-2270
      </span>
      <span class="contact-item">
        <svg width="20" height="20" viewBox="0 0 24 24" fill="none" stroke="var(--green)" stroke-width="2"><rect x="3" y="5" width="18" height="14" rx="1"/><path d="M3 6l9 7 9-7"/></svg>
        dana@o-vardex.org
      </span>
    </div>
    <div class="contact-line">
      <span class="contact-item">
        <svg width="20" height="20" viewBox="0 0 24 24" fill="none" stroke="var(--green)" stroke-width="2"><circle cx="12" cy="12" r="9"/><path d="M3 12h18M12 3c3 3 3 15 0 18M12 3c-3 3-3 15 0 18"/></svg>
        www.o-vardex.org
      </span>
    </div>
  </div>
</div>
</body>
</html>
```